RW Holloway LLC Business Card - Civil Engineering & Consulting Firm

We need a Business Card that is elegant, and masculine.  It is our Professional Civil Engineering & Consulting Company located in San Antonio TX (Not s construction or builder firm- no gears & no tool images please). We provide civil engineering services including  commercial site plans, grading and drainage plans, utility plans, hydraulics and hydrology, land planning, utility coordination, and other general civil engineering services related to commercial and residential development.
We have 2 existing Logos. We would like to convey reliability, strength, trustworthiness and attention to detail.  Blues and orange tones as per logo We are OK with the use of a darker blue in the mix.  We have 2 logo versions - Full Company Name Logo to go on the back of card, & Small Icon Logo for the front w/ personal Info.

Target Market(s)
Architects, Real Estate Developers, Other Strctural Engineers, Surveyers, General Contractors
Industry/Entity Type
Professional Civil Engineering
Contact Information for Business Card
Name, Position, Address, Cell & Office #, email, and company website
Font styles to use
Other font styles liked:
- Avian
Requirements
Should not have
- No Tools, No Gears, no Cranes, or Construction Equipment.

```html
<!DOCTYPE html>
<html lang="en">
<head>
<meta charset="utf-8">
<title>RW Holloway LLC Business Card</title>
<link href="https://fonts.googleapis.com/css2?family=Questrial&family=Montserrat:wght@700&display=swap" rel="stylesheet">
<style>
  :root {
    --navy: #0d2545;
    --orange: #f28c1e;
    --sky: #79acd9;
    --white: #f4f6f9;
    --backdrop: #26282b;
  }
  html, body {
    margin: 0;
    padding: 0;
    overflow: hidden;
  }
  .canvas {
    width: 1200px;
    height: 874px;
    background: var(--backdrop);
    display: flex;
    flex-direction: column;
    align-items: center;
    justify-content: center;
    gap: 34px;
    font-family: "Questrial", sans-serif;
  }
  .card {
    position: relative;
    width: 620px;
    height: 354px;
    box-sizing: border-box;
    background: var(--navy);
    border-style: solid;
    border-width: 12px;
  }
  .card--back {
    border-color: var(--orange) var(--sky) var(--sky) var(--orange);
  }
  .card--front {
    border-color: var(--sky) var(--orange) var(--orange) var(--sky);
  }
  .company-name {
    position: absolute;
    left: 0;
    right: 0;
    top: 50%;
    transform: translateY(-50%);
    text-align: center;
    color: var(--sky);
    font-size: 44px;
    letter-spacing: 6px;
    text-transform: uppercase;
  }
  .person {
    position: absolute;
    right: 350px;
    top: 108px;
    text-align: right;
  }
  .person__name {
    font-family: "Montserrat", sans-serif;
    font-weight: 700;
    color: var(--orange);
    font-size: 22px;
    letter-spacing: -0.5px;
    text-transform: uppercase;
    margin: 0;
  }
  .person__title {
    color: var(--sky);
    font-size: 16px;
    margin: 2px 0 0;
  }
  .divider {
    position: absolute;
    left: 262px;
    top: 110px;
    width: 1px;
    height: 88px;
    background: var(--sky);
    opacity: 0.6;
  }
  .contacts {
    position: absolute;
    left: 280px;
    top: 112px;
    margin: 0;
    padding: 0;
    list-style: none;
    color: var(--white);
    font-size: 16px;
    line-height: 21px;
  }
  .contacts li {
    display: flex;
    align-items: center;
    gap: 8px;
  }
  .contacts svg {
    width: 11px;
    height: 11px;
    flex: none;
  }
  .address {
    position: absolute;
    left: 120px;
    top: 228px;
    margin: 0;
    color: var(--white);
    font-size: 15px;
  }
  .corner-name {
    position: absolute;
    right: 22px;
    bottom: 18px;
    color: var(--orange);
    font-size: 13px;
    letter-spacing: 1px;
    text-transform: uppercase;
  }
</style>
</head>
<body>
<main class="canvas">
  <section class="card card--back" aria-label="Card back">
    <div class="company-name">RW Holloway LLC</div>
  </section>

  <section class="card card--front" aria-label="Card front">
    <div class="person">
      <h1 class="person__name">Daniel Reyes</h1>
      <p class="person__title">President</p>
    </div>
    <div class="divider"></div>
    <ul class="contacts">
      <li>
        <svg viewBox="0 0 12 12" aria-hidden="true"><path d="M2.5 1 L4.5 1 L5.2 3.6 L4 4.6 Q5 7 7.4 8 L8.4 6.8 L11 7.5 L11 9.5 Q11 11 9.5 11 Q1 10 1 2.5 Q1 1 2.5 1Z" fill="var(--orange)"/></svg>
        <span>210-555-0147</span>
      </li>
      <li>
        <svg viewBox="0 0 12 12" aria-hidden="true"><rect x="3" y="0.8" width="6" height="10.4" rx="1" fill="none" stroke="var(--orange)" stroke-width="1.4"/><circle cx="6" cy="9.3" r="0.7" fill="var(--orange)"/></svg>
        <span>210-555-0193</span>
      </li>
      <li>
        <svg viewBox="0 0 12 12" aria-hidden="true"><rect x="0.5" y="2.5" width="11" height="7.5" fill="var(--orange)"/><path d="M0.8 2.8 L6 7 L11.2 2.8" fill="none" stroke="var(--navy)" stroke-width="1"/></svg>
        <span>reyes@rwholloway.com</span>
      </li>
      <li>
        <svg viewBox="0 0 12 12" aria-hidden="true"><circle cx="6" cy="6" r="5" fill="none" stroke="var(--orange)" stroke-width="1.3"/><ellipse cx="6" cy="6" rx="2" ry="5" fill="none" stroke="var(--orange)" stroke-width="1"/><line x1="1" y1="6" x2="11" y2="6" stroke="var(--orange)" stroke-width="1"/></svg>
        <span>www.rwholloway.com</span>
      </li>
    </ul>
    <p class="address">4120 Cedar Bend Drive, San Antonio, Texas 78230</p>
    <div class="corner-name">RW Holloway LLC</div>
  </section>
</main>
</body>
</html>
```